Business card for my new company (Accounting firm)

I need a business card for my new business Brightwell Advisory and Ledger SA. Our services are accounting, tax, audit and financial management. Our customers are small companies, start-ups and new companies. The final design has to show financial security, trust and growth. Please find our logo attached to the business card. Text for the business card: Brightwell Advisory and Ledger SA Tomas Varenholt Director and Founder Certified Accountant Tel. 022 418 57 34 tv@clairevalconseil.ch www.clairevalconseil.ch Rue des Vergières 27 1201 Geneva
Target Market(s)
Our customers are small companies, start-ups and new companies.
Industry/Entity Type
Finance And Accounting
Contact Information for Business Card
Claireval Conseil et Comptes SA
Tomas Varenholt
Directeur et Fondateur
Expert-comptable diplômé
Tél. 022 418 57 34
tv@clairevalconseil.ch
www.clairevalconseil.ch
Rue des Vergières 27
1201 Genève

```html
<!DOCTYPE html>
<html lang="fr">
<head>
<meta charset="utf-8">
<title>Claireval Conseil et Comptes SA – Carte de visite</title>
<link rel="stylesheet" href="https://fonts.googleapis.com/css2?family=Montserrat:wght@400;500;600;700&display=swap">
<style>
  :root {
    --backdrop: #3b3c40;
    --card: #1c1d21;
    --card-gloss: #2b2c31;
    --blue: #2aa3de;
    --blue-deep: #1f78c0;
    --white: #ffffff;
    --muted: #b9bcc4;
  }
  * { box-sizing: border-box; margin: 0; padding: 0; }
  html, body {
    width: 800px;
    height: 1200px;
    overflow: hidden;
    background: var(--backdrop);
    font-family: "Montserrat", Arial, sans-serif;
  }
  .canvas {
    position: relative;
    width: 800px;
    height: 1200px;
  }
  .card {
    position: absolute;
    left: 60px;
    width: 680px;
    height: 440px;
    background: var(--card);
    border-radius: 6px;
    overflow: hidden;
    box-shadow: 0 18px 40px rgba(0,0,0,0.35);
  }
  .card--front { top: 110px; }
  .card--back  { top: 650px; }

  /* Front */
  .front-brand {
    position: absolute;
    inset: 0 0 16px 0;
    display: flex;
    flex-direction: column;
    align-items: center;
    justify-content: center;
    gap: 16px;
  }
  .front-brand__mark {
    width: 70px;
    height: 70px;
    background: var(--card-gloss);
  }
  .front-brand__name {
    color: var(--card-gloss);
    font-weight: 600;
    text-align: center;
    text-transform: uppercase;
    line-height: 1.1;
  }
  .front-brand__name .primary { display: block; font-size: 50px; letter-spacing: 4px; }
  .front-brand__name .secondary { display: block; font-size: 15px; letter-spacing: 5px; margin-top: 6px; }
  .front-edge {
    position: absolute;
    left: 0; right: 0; bottom: 0;
    height: 16px;
    background: var(--blue);
  }

  /* Back */
  .back-content {
    position: absolute;
    left: 46px;
    top: 40px;
    color: var(--white);
  }
  .back-brand {
    font-weight: 600;
    text-transform: uppercase;
    color: var(--white);
    line-height: 1.1;
  }
  .back-brand .primary { display: block; font-size: 40px; letter-spacing: 3px; }
  .back-brand .secondary { display: block; font-size: 15px; letter-spacing: 4px; margin-top: 4px; }
  .person { margin-top: 34px; }
  .person__name {
    color: var(--blue);
    font-size: 22px;
    font-weight: 600;
  }
  .person__role {
    color: var(--muted);
    font-size: 13px;
    line-height: 1.45;
    margin-top: 4px;
  }
  .contacts {
    list-style: none;
    margin-top: 16px;
    font-size: 13px;
    color: var(--white);
  }
  .contacts li {
    display: flex;
    align-items: center;
    gap: 10px;
    margin-bottom: 7px;
  }
  .contacts svg {
    width: 18px;
    height: 18px;
    flex: none;
  }
  .address {
    margin-top: 10px;
    font-size: 13px;
    color: var(--muted);
  }
</style>
</head>
<body>
<main class="canvas">

  <section class="card card--front" aria-label="Recto de la carte">
    <div class="front-brand">
      <div class="front-brand__mark"></div>
      <div class="front-brand__name">
        <span class="primary">Claireval</span>
        <span class="secondary">Conseil et Comptes</span>
      </div>
    </div>
    <div class="front-edge"></div>
  </section>

  <section class="card card--back" aria-label="Verso de la carte">
    <div class="back-content">
      <div class="back-brand">
        <span class="primary">Claireval</span>
        <span class="secondary">Conseil et Comptes</span>
      </div>

      <div class="person">
        <p class="person__name">Tomas Varenholt</p>
        <p class="person__role">Directeur et Fondateur<br>Expert-comptable diplômé</p>
      </div>

      <ul class="contacts">
        <li>
          <svg viewBox="0 0 24 24" aria-hidden="true"><circle cx="12" cy="12" r="12" fill="var(--blue-deep)"/><path d="M8.5 6.5l2 2.5-1.2 1.4a8 8 0 0 0 4.3 4.3l1.4-1.2 2.5 2-1.2 2c-4.6 0-9.3-4.7-9.3-9.3z" fill="#fff"/></svg>
          <span>Tél. 022 418 57 34</span>
        </li>
        <li>
          <svg viewBox="0 0 24 24" aria-hidden="true"><circle cx="12" cy="12" r="12" fill="var(--blue-deep)"/><rect x="6" y="8" width="12" height="8.5" rx="1" fill="#fff"/><path d="M6.3 8.5L12 13l5.7-4.5" stroke="var(--blue-deep)" stroke-width="1.3" fill="none"/></svg>
          <span>tv@clairevalconseil.ch</span>
        </li>
        <li>
          <svg viewBox="0 0 24 24" aria-hidden="true"><circle cx="12" cy="12" r="12" fill="var(--blue-deep)"/><circle cx="12" cy="12" r="6" stroke="#fff" stroke-width="1.3" fill="none"/><path d="M6 12h12M12 6c-2.6 3.5-2.6 8.5 0 12M12 6c2.6 3.5 2.6 8.5 0 12" stroke="#fff" stroke-width="1.1" fill="none"/></svg>
          <span>www.clairevalconseil.ch</span>
        </li>
      </ul>

      <p class="address">Rue des Vergières 27, 1201 Genève</p>
    </div>
  </section>

</main>
</body>
</html>
```